New Business card design to reflect rebrand

I would like a business card design with a good base colour for our new logo and also a placeholder for a profile pic of the card holder. the design needs to be editable to the point that we can easily change the picture of the person and use that design for printmerlo etc. we are looking at a metalic finish business card so will need a good base colour to bring out the finish.

Target Market(s)

prospective customers

Industry/Entity Type

Business

Contact Information for Business Card

I would like one editable design that we can change the name of the card holder and profile picture. The design need to be in a format that be send to printmerlo etc.

Our address is Fenwick Lodge, Copse Lane, Elmsford Vale, GU14 3TP Tel no. 01483 556172

Requirements
Must have
• place holder for a profile pic for the card holder. in AI or preferably PSD format

```html
<!DOCTYPE html>
<html lang="en">
<head>
<meta charset="utf-8">
<title>Veldmark Workplace Services – Business Card</title>
<link rel="stylesheet" href="https://fonts.googleapis.com/css2?family=Montserrat:wght@600;700&family=Open+Sans:wght@400;600&display=swap">
<style>
  :root {
    --canvas: #ecebe9;
    --card-top: #f4f2f0;
    --brand-orange: #ec6408;
    --brand-slate: #3e4a5c;
    --white: #ffffff;
    --photo-light: #d9d4cf;
    --photo-dark: #2b2d3a;
  }
  * { box-sizing: border-box; margin: 0; padding: 0; }
  html, body { width: 1200px; height: 900px; overflow: hidden; }
  body {
    position: relative;
    background: var(--canvas);
    font-family: "Open Sans", Arial, sans-serif;
  }
  .card {
    position: absolute;
    background: var(--card-top);
    overflow: hidden;
    box-shadow: 0 6px 18px rgba(0,0,0,0.18);
  }
  .card--front { left: 497px; top: 80px; width: 560px; height: 343px; }
  .card--back  { left: 128px; top: 445px; width: 555px; height: 343px; }

  .band {
    position: absolute;
    background: var(--brand-orange);
  }
  .card--front .band { left: 0; top: 170px; width: 340px; height: 173px; }
  .card--back .band  { left: 134px; top: 172px; width: 421px; height: 171px; }

  .portrait {
    position: absolute;
    top: 0;
    width: 227px;
    height: 343px;
    background: linear-gradient(180deg, var(--photo-light) 0%, var(--photo-light) 35%, #6d6a70 60%, var(--photo-dark) 100%);
  }
  .card--front .portrait { right: 0; }
  .card--back .portrait { left: 0; }

  .brand-mark {
    position: absolute;
    left: 29px;
    top: 98px;
    font-family: "Montserrat", Arial, sans-serif;
  }
  .brand-mark__name {
    font-weight: 700;
    font-size: 40px;
    letter-spacing: 2.4px;
    color: var(--brand-slate);
    line-height: 1;
  }
  .brand-mark__tagline {
    margin-top: 8px;
    font-weight: 600;
    font-size: 16px;
    letter-spacing: 3.4px;
    color: var(--brand-orange);
    line-height: 1;
  }

  .holder {
    position: absolute;
    left: 29px;
    top: 183px;
    color: var(--white);
  }
  .holder__name {
    font-weight: 600;
    font-size: 19px;
    margin-bottom: 13px;
  }
  .holder__line {
    display: flex;
    align-items: center;
    gap: 8px;
    font-size: 14px;
    line-height: 23px;
  }
  .holder__line svg { width: 11px; height: 11px; }
  .holder__address {
    margin-top: 10px;
    font-size: 14px;
    line-height: 21px;
  }

  .back-brand {
    position: absolute;
    left: 262px;
    top: 230px;
    color: var(--white);
    font-family: "Montserrat", Arial, sans-serif;
  }
  .back-brand__name {
    font-weight: 700;
    font-size: 37px;
    letter-spacing: 3.6px;
    line-height: 1;
  }
  .back-brand__tagline {
    margin-top: 6px;
    font-weight: 600;
    font-size: 16px;
    letter-spacing: 3.4px;
    line-height: 1;
  }
</style>
</head>
<body>

  <section class="card card--front" aria-label="Business card front">
    <div class="brand-mark">
      <div class="brand-mark__name">VELDMARK</div>
      <div class="brand-mark__tagline">WORKPLACE SERVICES</div>
    </div>
    <div class="band"></div>
    <div class="holder">
      <p class="holder__name">Daniel Hart</p>
      <p class="holder__line">
        <svg viewBox="0 0 24 24" aria-hidden="true"><path fill="#ffffff" d="M6.6 10.8a15 15 0 0 0 6.6 6.6l2.2-2.2c.3-.3.7-.4 1-.2 1.1.4 2.3.6 3.6.6.6 0 1 .4 1 1V20c0 .6-.4 1-1 1C10.6 21 3 13.4 3 4c0-.6.4-1 1-1h3.5c.6 0 1 .4 1 1 0 1.3.2 2.5.6 3.6.1.3 0 .7-.2 1z"/></svg>
        01483 556172
      </p>
      <p class="holder__line">
        <svg viewBox="0 0 24 24" aria-hidden="true"><rect x="2" y="5" width="20" height="14" fill="#ffffff"/><path d="M2 5l10 8 10-8" fill="none" stroke="#ec6408" stroke-width="2"/></svg>
        info@veldmark.com
      </p>
      <p class="holder__address">Fenwick Lodge, Copse Lane,<br>Elmsford Vale, GU14 3TP</p>
    </div>
    <div class="portrait" role="img" aria-label="Profile photo of the card holder in a dark suit"></div>
  </section>

  <section class="card card--back" aria-label="Business card back">
    <div class="band"></div>
    <div class="portrait" role="img" aria-label="Profile photo of the card holder in a dark suit"></div>
    <div class="back-brand">
      <div class="back-brand__name">VELDMARK</div>
      <div class="back-brand__tagline">WORKPLACE SERVICES</div>
    </div>
  </section>

</body>
</html>
```